Web Design Project

We have a website in beta that needs updating and are looking for a freash new look for the Home page including Logo.
Our company is called " Kip Dorra " we specialize in classified advertising using video. Our consumers will be businesses selling a product or service. Please visit www.kipdorra.com
Our aim past this point is to engage a developer to write the code based on the best design. Our target market is the U.S and I have included some of the landing pages to give you a better idea of what we are trying to acheive

http://www.kipdorra.com/
http://www.kipdorra.com/cars_home.php
http://www.kipdorra.com/boats.php
http://www.kipdorra.com/electronic.php
http://www.kipdorra.com/realestate.php
http://www.kipdorra.com/roommates.php
Updates

Target Market(s)

20-35 yr old people who are connected to the internet via mobile phone and use social media on a daily/weekly basis

Industry/Entity Type

Advertising

Requirements
Must have
• We would like to use lots of images to convey it is a video driven website business
Nice to have
• Logo to incorporate same theme of website ( ie ) you are here to watch videos of thinhs to buy & sell
Should not have
• This is to be a freash new site with large type and bold fonts

```html
<!DOCTYPE html>
<html lang="en">
<head>
<meta charset="utf-8">
<title>Kip Dorra — Video Classifieds</title>
<link rel="stylesheet" href="https://fonts.googleapis.com/css2?family=Open+Sans:wght@400;600;700&family=Arimo:wght@400;700&display=swap">
<style>
:root{
  --black:#050505;
  --panel:#1b1b1b;
  --panel-line:#2c2c2c;
  --band:#262626;
  --footer:#1a1a1a;
  --bottom:#111;
  --yellow:#f2d200;
  --yellow-light:#fff04a;
  --yellow-text:#e8c600;
  --green:#4ea60b;
  --red:#d8262a;
  --text-light:#e9e9e9;
  --text-mid:#b5b5b5;
  --text-dim:#8a8a8a;
  --text-faint:#6f6f6f;
}
*{box-sizing:border-box;margin:0;padding:0}
html,body{width:900px;height:1200px;overflow:hidden}
body{position:relative;background:var(--black);font-family:"Open Sans",Arial,sans-serif;color:var(--text-light)}
.abs{position:absolute}

/* header */
.site-header{position:absolute;left:0;top:0;width:900px;height:712px;background:linear-gradient(#151515 0,#050505 140px,#0a0a0a 712px)}
.top-rule{position:absolute;left:0;top:0;width:900px;height:3px;background:#2a2a2a}
.brand{left:113px;top:14px}
.brand-name{display:flex;align-items:center;gap:6px;font-weight:700;font-size:29px;color:#fff;line-height:1}
.brand-dot{width:14px;height:14px;border-radius:50%;background:var(--red)}
.brand-tag{font-size:10px;font-weight:700;margin-top:11px;color:#fff}
.brand-rank{font-size:15px;font-weight:700;color:#fff;margin-top:1px}
.account-tabs{left:632px;top:3px;display:flex;gap:3px}
.account-tabs a{display:block;height:24px;padding:0 10px;line-height:24px;font-family:Arimo,Arial,sans-serif;font-weight:700;font-size:10px;color:#fff;text-decoration:none;background:linear-gradient(#444,#2b2b2b);border-radius:0 0 4px 4px}
.support{left:658px;top:44px;font-size:12px;line-height:14px}
.support b{color:var(--text-mid);font-weight:700}
.support span{display:block;color:#fff;font-weight:600}

/* nav */
.main-nav{left:113px;top:99px;width:674px;height:34px;border-radius:3px;background:linear-gradient(var(--yellow-light),var(--yellow) 55%,#e4c000);display:flex}
.main-nav a{display:block;height:34px;line-height:34px;padding:0 13px 0 9px;font-family:Arimo,Arial,sans-serif;font-weight:700;font-size:14px;color:#111;text-decoration:none;border-right:1px solid #cfae00;box-shadow:1px 0 0 #fff46e}
.search{left:603px;top:103px;width:179px;height:26px;display:flex}
.search-field{width:152px;height:26px;background:#fff;border-radius:3px 0 0 3px;font-size:9px;color:#9a9a9a;line-height:26px;padding-left:8px}
.search-btn{width:27px;height:26px;background:linear-gradient(#e6e6e6,#c9c9c9);border-radius:0 3px 3px 0}

/* hero */
.hero{left:113px;top:153px;width:674px;height:278px;border-radius:3px;overflow:hidden;background:linear-gradient(90deg,#b8902a 0%,#c9aa4f 30%,#e8d27c 60%,#f1da6a 85%,#eacb3e 100%)}
.hero-photo{position:absolute;left:0;top:0;width:360px;height:278px;background:radial-gradient(ellipse at 45% 50%,#6c6d6b 0 38%,rgba(200,160,110,.8) 55%,rgba(0,0,0,0) 75%)}
.hero-title{left:399px;top:106px;font-size:32px;color:#111;font-weight:400;letter-spacing:-.3px;text-shadow:0 1px 2px rgba(255,255,255,.5)}
.hero-cta{left:434px;top:187px;width:157px;height:39px;background:linear-gradient(#5cbc14,var(--green));border-radius:2px;color:#fff;font-size:21px;text-align:center;line-height:39px}

/* categories */
.categories{left:113px;top:450px;width:159px;height:242px;background:var(--panel);border-radius:3px;overflow:hidden}
.categories h2{height:34px;line-height:34px;padding-left:10px;font-family:Arimo,Arial,sans-serif;font-size:14px;font-weight:700;color:#111;background:linear-gradient(#dcdcdc,#9c9c9c)}
.category-list{list-style:none;padding:0 6px}
.category-list li{height:32px;display:flex;align-items:center;gap:11px;padding-left:2px;font-size:12px;color:var(--text-mid);border-bottom:1px solid var(--panel-line)}
.category-list li:first-child{margin-top:5px}
.category-list li:last-child{border-bottom:0}
.category-list svg{width:20px;height:18px;flex:none}

/* video tabs */
.video-tabs{left:295px;top:450px;display:flex;gap:9px}
.video-tabs span{display:block;height:35px;line-height:35px;padding:0 14px;font-size:16px;color:#7d7d7d;background:#1c1c1c;border-radius:3px 3px 0 0}
.video-tabs .active{color:#fff;font-weight:600;background:#222}
.video-panel{left:288px;top:485px;width:499px;height:207px;background:var(--panel);border:1px solid var(--panel-line);border-radius:3px}
.thumb{position:absolute;width:104px;height:78px}
.thumb::after{content:"";position:absolute;left:41px;top:28px;width:22px;height:20px;background:rgba(216,38,42,.85);border-radius:3px}
.thumb::before{content:"";position:absolute;left:49px;top:33px;border-left:9px solid #fff;border-top:5px solid transparent;border-bottom:5px solid transparent;z-index:1}

/* how it works */
.how-band{left:0;top:712px;width:900px;height:305px;background:var(--band);background-image:repeating-linear-gradient(45deg,rgba(255,255,255,.02) 0 1px,transparent 1px 3px)}
.how-title{left:0;top:738px;width:900px;text-align:center;font-family:Arimo,Arial,sans-serif;font-weight:700;font-size:16px;color:var(--yellow-text)}
.how-rule{top:745px;height:4px;background:repeating-linear-gradient(90deg,#555 0 3px,transparent 3px 5px)}
.step{top:786px;width:170px;height:210px;text-align:center}
.step-disc{width:170px;height:162px;border-radius:50%;background:#161616;box-shadow:inset 0 2px 6px #000;display:flex;align-items:center;justify-content:center}
.step-disc svg{width:150px;height:150px}
.step-label{margin-top:20px;font-family:Arimo,Arial,sans-serif;font-size:17px;color:#ddd}

/* footer */
.site-footer{left:0;top:1017px;width:900px;height:153px;background:var(--footer)}
.footer-col{position:absolute;top:1035px}
.footer-col h3{font-size:12px;font-weight:600;color:#fff;margin-bottom:6px}
.footer-col a{display:block;font-size:9.5px;color:var(--text-dim);text-decoration:none;line-height:17px}
.follow-item{display:flex;align-items:center;gap:7px;height:38px;font-size:9.5px;color:var(--text-dim)}
.follow-item i{width:26px;height:26px;border-radius:3px;display:block}
.copyright{left:0;top:1170px;width:900px;height:30px;background:var(--bottom);font-size:9px;color:var(--text-faint);text-align:center;line-height:30px}
</style>
</head>
<body>

<header class="site-header">
  <div class="top-rule"></div>
  <div class="abs brand">
    <div class="brand-name"><span>Kip Dorra</span><span class="brand-dot"></span></div>
    <div class="brand-tag">Buy and sell through the</div>
    <div class="brand-rank">#1 Video Classifieds</div>
  </div>
  <nav class="abs account-tabs"><a href="#">SIGN IN</a><a href="#">CREATE AN AD</a></nav>
  <div class="abs support"><b>Support</b><span>support@kipdorra.com</span></div>

  <nav class="abs main-nav">
    <a href="#" style="padding-left:9px">HOME</a><a href="#">BUY</a><a href="#">SELL</a><a href="#">INFO</a><a href="#">CONTACT US</a>
  </nav>
  <div class="abs search">
    <div class="search-field">Search key word</div>
    <div class="search-btn">
      <svg width="27" height="26" viewBox="0 0 27 26"><circle cx="12" cy="11.5" r="5" fill="none" stroke="#333" stroke-width="2.2"/><line x1="15.5" y1="15" x2="20" y2="19.5" stroke="#333" stroke-width="2.6"/></svg>
    </div>
  </div>

  <section class="abs hero">
    <div class="hero-photo" role="img" aria-label="Hand holding a smartphone playing a car sales video over a blurred warm background"></div>
    <div class="abs hero-title">Online Markiting</div>
    <div class="abs hero-cta">Start Now!</div>
  </section>

  <aside class="abs categories">
    <h2>CATEGORIES</h2>
    <ul class="category-list">
      <li><svg viewBox="0 0 20 18"><path d="M2 12V9l2-4h12l2 4v3z" fill="none" stroke="#ddd" stroke-width="1.6"/><circle cx="5.5" cy="13" r="1.8" fill="#ddd"/><circle cx="14.5" cy="13" r="1.8" fill="#ddd"/></svg>Car</li>
      <li><svg viewBox="0 0 20 18"><path d="M9 2v10H3zM11 4v8h6z" fill="#ddd"/><path d="M1 13h18l-2 3H3z" fill="#ddd"/></svg>Boats</li>
      <li><svg viewBox="0 0 20 18"><rect x="2" y="5" width="16" height="11" rx="1" fill="none" stroke="#ddd" stroke-width="1.6"/><path d="M7 1l3 4 3-4" fill="none" stroke="#ddd" stroke-width="1.4"/><rect x="5" y="8" width="8" height="5" fill="#ddd"/></svg>Electronics</li>
      <li><svg viewBox="0 0 20 18"><path d="M10 1L1 9h3v8h4v-5h4v5h4V9h3z" fill="#fff"/></svg>Real Estate</li>
      <li><svg viewBox="0 0 20 18"><circle cx="9" cy="8" r="5" fill="none" stroke="#ddd" stroke-width="1.6"/><line x1="12.5" y1="11.5" x2="17" y2="16" stroke="#ddd" stroke-width="2"/><circle cx="9" cy="8" r="1.6" fill="#ddd"/></svg>Roommat</li>
      <li><svg viewBox="0 0 20 18"><path d="M2 9h14M11 3l6 6-6 6" fill="none" stroke="#fff" stroke-width="2"/></svg>Other Categories</li>
    </ul>
  </aside>

  <div class="abs video-tabs"><span class="active">Most Viewed</span><span>Most Recent</span><span>Most Interesting</span></div>
  <section class="abs video-panel">
    <div class="thumb" style="left:16px;top:17px;background:linear-gradient(135deg,#8aa8c0,#3d6d92 60%,#9bb36a)" role="img" aria-label="Video: car for sale"></div>
    <div class="thumb" style="left:137px;top:17px;background:linear-gradient(135deg,#6b4a2a,#c79a5e 55%,#efe0c2)" role="img" aria-label="Video: furnished living room"></div>
    <div class="thumb" style="left:258px;top:17px;background:linear-gradient(135deg,#d9d9d9,#8b8f95 55%,#ece8e2)" role="img" aria-label="Video: laptop seller"></div>
    <div class="thumb" style="left:378px;top:17px;background:linear-gradient(135deg,#e8e6e6,#c73a43 55%,#f2efef)" role="img" aria-label="Video: shopping bags"></div>
    <div class="thumb" style="left:16px;top:112px;background:linear-gradient(135deg,#c9cfd6,#3d3f45 55%,#e9ecef)" role="img" aria-label="Video: snowmobile"></div>
    <div class="thumb" style="left:137px;top:112px;background:linear-gradient(180deg,#dbe6ee,#a19c94 55%,#4f6b3a)" role="img" aria-label="Video: house for sale"></div>
    <div class="thumb" style="left:258px;top:112px;background:linear-gradient(135deg,#f0efee,#9a9a9a 55%,#d44b4b)" role="img" aria-label="Video: electronics store"></div>
    <div class="thumb" style="left:378px;top:112px;background:linear-gradient(135deg,#2a4f85,#5577a8 55%,#1f3f6e)" role="img" aria-label="Video: airplane"></div>
  </section>
</header>

<section class="abs how-band"></section>
<div class="abs how-rule" style="left:113px;width:272px"></div>
<div class="abs how-rule" style="left:515px;width:272px"></div>
<h2 class="abs how-title">HOW IT WORK</h2>

<svg width="0" height="0" style="position:absolute">
  <defs>
    <radialGradient id="discFace" cx="40%" cy="30%" r="75%"><stop offset="0" stop-color="#f4f4f4"/><stop offset=".6" stop-color="#d6d6d6"/><stop offset="1" stop-color="#a9a9a9"/></radialGradient>
  </defs>
</svg>

<div class="abs step" style="left:143px">
  <div class="step-disc"><svg viewBox="0 0 150 150"><circle cx="75" cy="75" r="74" fill="url(#discFace)"/>
    <g fill="#8d8d8d"><rect x="53" y="34" width="44" height="82" rx="2"/></g>
    <g fill="#d9d9d9"><rect x="63" y="40" width="24" height="30"/><rect x="63" y="80" width="24" height="30"/>
    <rect x="56" y="40" width="4" height="6"/><rect x="56" y="52" width="4" height="6"/><rect x="56" y="64" width="4" height="6"/><rect x="56" y="76" width="4" height="6"/><rect x="56" y="88" width="4" height="6"/><rect x="56" y="100" width="4" height="6"/>
    <rect x="90" y="40" width="4" height="6"/><rect x="90" y="52" width="4" height="6"/><rect x="90" y="64" width="4" height="6"/><rect x="90" y="76" width="4" height="6"/><rect x="90" y="88" width="4" height="6"/><rect x="90" y="100" width="4" height="6"/></g>
  </svg></div>
  <div class="step-label">CREATE IT</div>
</div>
<div class="abs step" style="left:364px">
  <div class="step-disc"><svg viewBox="0 0 150 150"><circle cx="75" cy="75" r="74" fill="url(#discFace)"/>
    <rect x="40" y="42" width="70" height="50" rx="3" fill="#8d8d8d"/><rect x="46" y="48" width="58" height="38" fill="#d6d6d6"/>
    <path d="M70 92h10l3 12H67z" fill="#8d8d8d"/><rect x="58" y="104" width="34" height="4" fill="#8d8d8d"/>
    <path d="M75 52l10 11h-6v14h-8V63h-6z" fill="#8d8d8d"/>
  </svg></div>
  <div class="step-label">UPLOAD IT</div>
</div>
<div class="abs step" style="left:589px">
  <div class="step-disc"><svg viewBox="0 0 150 150"><circle cx="75" cy="75" r="74" fill="url(#discFace)"/>
    <path d="M80 38h34v34l-44 44-34-34z" fill="#8d8d8d"/><circle cx="102" cy="50" r="5" fill="#d6d6d6"/>
  </svg></div>
  <div class="step-label">SELL IT</div>
</div>

<footer class="abs site-footer"></footer>
<div class="footer-col" style="left:113px"><h3>Buy /&nbsp; Browse</h3><a href="#">Roommates</a><a href="#">Cars</a><a href="#">Electronics</a><a href="#">Boats</a><a href="#">Others</a></div>
<div class="footer-col" style="left:260px"><h3>Sell</h3><a href="#">Start Selling</a><a href="#">Login</a><a href="#">Shooting</a><a href="#">Uploading</a><a href="#">Buying</a></div>
<div class="footer-col" style="left:377px"><h3>Info</h3><a href="#">VBlog</a><a href="#">FAQs</a><a href="#">Terms of Use</a><a href="#">Privacy policy</a><a href="#">Buyer/Seller Safety</a></div>
<div class="footer-col" style="left:521px"><h3>Contact</h3><a href="#">Contact Us</a><a href="#">Feedback Form</a><a href="#">Referral Progam</a><a href="#">Business Register</a><a href="#">Subsrciption</a></div>
<div class="footer-col" style="left:656px"><h3>Follow Us</h3>
  <div class="follow-item"><i style="background:#3b5a9a"></i>Join Us on Friendly</div>
  <div class="follow-item"><i style="background:#4cb0d8"></i>Follow us on Chirper</div>
  <div class="follow-item"><i style="background:#e8632a"></i>RSS Feed</div>
</div>
<div class="abs copyright">Copyright © 2013 Kip Dorra. All right reserved.</div>

</body>
</html>
```